Property Services Company Needs a Brochure Design

Looking for a new brochure design for an existing property services company.

We provide a range of property services from, market research, real estate brokerage, valuation and appraisal, property development and other real estate consulting services.

We would like a fresh modern brochure design with good graphics and features. Our colours are white, blue and orange.

The design should communicate, attention to detail, superior service delivery and distinction in results.
Updates

I would like the brochure to be roughly about 20 pages.

Containing the following,

1) An introduction
2) Contents Page
2) What we do
3) Our Services
4) Agency & Brokerage
5) Real Estate Consulting
6) Market Research
7) Appraisal & Valuation
8) Project Management
9) Property Development

I would also like icons to represent items 4,5,6,7,8 & 9, they should be represented vertically on each of the pages from the contents page and highlighted individually on the pages that they represent.. i.e. on appraisal & valuation page, all six icons will be arranged vertically and the appraisal and valuations icon will be highlighted.

I will also like to have images that depict the services on the various pages.

I have some pages I think will flow which I will upload shortly.

Industry/Entity Type

Real Estate

Font styles to use
Serif

Colors
f78f20
0455a3

```html
<!DOCTYPE html>
<html lang="en">
<head>
<meta charset="utf-8">
<title>Harwell Property Services – Brochure Cover</title>
<link rel="stylesheet" href="https://fonts.googleapis.com/css2?family=Source+Sans+3:wght@400;600&display=swap">
<style>
  :root {
    --navy: #2b2566;
    --orange: #e5672a;
    --ink: #3a3a3a;
    --paper: #ffffff;
    --fold: #e4e4e4;
  }
  * { margin: 0; padding: 0; box-sizing: border-box; }
  html, body { width: 1200px; height: 857px; overflow: hidden; background: var(--paper); }
  body { font-family: "Source Sans 3", Arial, sans-serif; }

  .spread { position: relative; width: 1200px; height: 857px; background: var(--paper); }

  .band { position: absolute; left: 0; width: 1200px; height: 16px; display: flex; }
  .band--top { top: 0; }
  .band--bottom { bottom: 0; }
  .band span { display: block; height: 100%; }
  .band .n { background: var(--navy); }
  .band .o { background: var(--orange); }

  .fold { position: absolute; left: 600px; top: 16px; bottom: 16px; width: 1px; background: var(--fold); }

  .brand { display: flex; align-items: flex-start; gap: 10px; color: var(--ink); font-weight: 400; }
  .brand__mark { background: var(--navy); flex: none; }
  .brand__text { display: flex; flex-direction: column; line-height: 1; }
  .brand__tag { align-self: flex-end; }

  /* Back cover */
  .back-cover { position: absolute; left: 0; top: 16px; width: 600px; height: 825px; }
  .back-cover .brand { position: absolute; left: 0; right: 0; top: 654px; justify-content: center; }
  .back-cover .brand__mark { width: 14px; height: 14px; margin-top: 14px; }
  .back-cover .brand__name { font-size: 40px; }
  .back-cover .brand__tag { font-size: 14px; margin-top: 0; margin-right: 20px; }

  .contact { position: absolute; left: 0; right: 0; top: 732px; text-align: center; font-family: Arial, Helvetica, sans-serif; color: #2f2f2f; font-style: normal; }
  .contact__line { display: flex; justify-content: center; align-items: center; gap: 20px; white-space: nowrap; }
  .contact__item { display: inline-flex; align-items: center; gap: 4px; }
  .contact__line--addr { font-size: 14.5px; }
  .contact__line--phone { font-size: 16.5px; margin-top: 4px; }
  .contact__line--web { font-size: 13.5px; margin-top: 3px; gap: 10px; }
  .icon { width: 12px; height: 12px; fill: var(--orange); flex: none; }

  /* Front cover */
  .front-cover { position: absolute; left: 600px; top: 16px; width: 600px; height: 825px; }
  .front-cover .brand { position: absolute; left: 0; right: 0; top: 68px; justify-content: center; }
  .front-cover .brand__mark { width: 18px; height: 18px; margin-top: 22px; }
  .front-cover .brand__name { font-size: 58px; }
  .front-cover .brand__tag { font-size: 18px; margin-top: -2px; margin-right: 34px; }

  .rule { position: absolute; left: 0; width: 600px; height: 13px; display: flex; }
  .rule span { height: 100%; }
  .rule--above { top: 198px; }
  .rule--below { top: 610px; }

  .hero-photo {
    position: absolute; left: 0; top: 211px; width: 600px; height: 399px;
    background: linear-gradient(100deg, #2a2a2a 0%, #5d5d5d 22%, #c9c9c9 45%, #eeeeee 65%, #d6d6d6 85%, #8e8e8e 100%);
  }

  .tagline {
    position: absolute; left: 0; right: 0; top: 645px;
    display: flex; justify-content: center; align-items: center;
    font-family: Arial, Helvetica, sans-serif;
    font-size: 33px; color: var(--navy); font-weight: 400;
  }
  .tagline__divider { width: 3px; height: 50px; background: var(--orange); margin: 0 10px; }

  .intro {
    position: absolute; left: 40px; width: 520px; top: 730px;
    font-size: 17px; line-height: 22px; color: var(--orange);
    white-space: nowrap;
  }
  .intro span { display: block; text-align: justify; text-align-last: justify; }
  .intro span:last-child { text-align-last: left; }
</style>
</head>
<body>
<main class="spread">
  <div class="band band--top"><span class="o" style="width:223px"></span><span class="n" style="width:753px"></span><span class="o" style="width:224px"></span></div>
  <div class="band band--bottom"><span class="n" style="width:223px"></span><span class="o" style="width:753px"></span><span class="n" style="width:224px"></span></div>
  <div class="fold"></div>

  <section class="back-cover">
    <div class="brand">
      <span class="brand__mark"></span>
      <div class="brand__text">
        <span class="brand__name">Harwell</span>
        <span class="brand__tag">Property Services</span>
      </div>
    </div>
    <address class="contact">
      <div class="contact__line contact__line--addr">
        <span class="contact__item">
          <svg class="icon" viewBox="0 0 12 12"><path d="M6 0a4 4 0 0 0-4 4c0 3 4 8 4 8s4-5 4-8a4 4 0 0 0-4-4zm0 5.5A1.5 1.5 0 1 1 6 2.5a1.5 1.5 0 0 1 0 3z"/></svg>
          9th Floor, Meridian House, 42 Marina Road Lagos, Nigeria
        </span>
      </div>
      <div class="contact__line contact__line--phone">
        <span class="contact__item">
          <svg class="icon" viewBox="0 0 12 12"><path d="M3 0l2 3-1.3 1.3a7 7 0 0 0 4 4L9 7l3 2-1.5 2.5C5 11 1 7 .5 1.5z"/></svg>
          +234 1 5550142
        </span>
        <span class="contact__item">
          <svg class="icon" viewBox="0 0 12 12"><rect x="3" y="1" width="6" height="3"/><rect x="0" y="4" width="12" height="5" rx="1"/><rect x="3" y="8" width="6" height="3"/></svg>
          +234 1 5550187
        </span>
      </div>
      <div class="contact__line contact__line--web">
        <span class="contact__item">
          <svg class="icon" viewBox="0 0 12 12"><circle cx="6" cy="6" r="5"/></svg>
          www.harwellps.com.ng
        </span>
        <span class="contact__item">
          <svg class="icon" viewBox="0 0 12 12" style="fill:none;stroke:var(--orange);stroke-width:1.2"><rect x="0.8" y="2" width="10.4" height="8"/><path d="M1 2.5l5 4 5-4"/></svg>
          info@harwellps.com.ng
        </span>
      </div>
    </address>
  </section>

  <section class="front-cover">
    <div class="brand">
      <span class="brand__mark"></span>
      <div class="brand__text">
        <span class="brand__name">Harwell</span>
        <span class="brand__tag">Property Services</span>
      </div>
    </div>
    <div class="rule rule--above"><span style="width:376px;background:var(--orange)"></span><span style="width:224px;background:var(--navy)"></span></div>
    <div class="hero-photo" role="img" aria-label="Photograph of a bright modern office with a glass desk, a mesh office chair and dark glass cabinets"></div>
    <div class="rule rule--below"><span style="width:376px;background:var(--navy)"></span><span style="width:224px;background:var(--orange)"></span></div>

    <h1 class="tagline">
      <span>Detail</span><span class="tagline__divider"></span><span>Delivery</span><span class="tagline__divider"></span><span>Distinction</span>
    </h1>
    <p class="intro">
      <span>We enjoy long-standing relationships with many of our clients and</span>
      <span>land lords, our lettings teams are always happy to meet with new</span>
      <span>clients to advise them on how best to maximise their rental return.</span>
    </p>
  </section>
</main>
</body>
</html>
```